Tovel & Associates - London New Letting and Property Management Company *

Tovel & Associates LTD is a new company based in London, and works with brand new residential property in the city centre.

We are aiming to have 1000 new properties a year.

We are looking for something modern and minimalistic :
Logo ,Monogram, Paper Head and Business Card.

Target Market(s)

Internation landlords

Industry/Entity Type

Real Estate

Logo Text

Tovel & Associates

Colors

Designer to choose colors to be used in the design.

Requirements
Nice to have
• A particular monogram with "TA"
Should not have
• Little House over the logo

```html
<!DOCTYPE html>
<html lang="en">
<head>
<meta charset="utf-8">
<title>Tovel &amp; Associates Stationery</title>
<link rel="stylesheet" href="https://fonts.googleapis.com/css2?family=Montserrat:wght@700&family=Work+Sans:wght@400;500&family=Lato:wght@400;700&display=swap">
<style>
:root{
  --navy:#1b4f72;
  --sky:#2aa3e0;
  --paper:#f3f3f3;
  --backdrop:#d9d9d9;
  --body-text:#7a7a7a;
  --dark-text:#555;
}
*{box-sizing:border-box;margin:0;padding:0}
html,body{width:1200px;height:1062px;overflow:hidden}
body{background:var(--backdrop);position:relative;font-family:"Work Sans",sans-serif}
.wordmark{font-family:"Montserrat",sans-serif;font-weight:700;color:var(--navy);letter-spacing:.04em;text-transform:uppercase;white-space:nowrap}
.mark-square{display:inline-block;background:var(--navy)}

/* letterhead */
.letterhead{position:absolute;left:115px;top:94px;width:620px;height:876px;background:var(--paper);overflow:hidden}
.letterhead .brand{position:absolute;right:45px;top:50px;text-align:center}
.letterhead .brand .mark-square{width:54px;height:54px;margin-bottom:16px}
.letterhead .brand .wordmark{font-size:15px;display:block}
.salutation{position:absolute;left:42px;top:190px;font-size:17px;color:var(--dark-text)}
.letter-body{position:absolute;left:42px;top:243px;width:536px}
.letter-body p{font-size:12px;line-height:16.2px;color:var(--body-text);margin-bottom:20px}
.signoff{position:absolute;left:42px;top:627px;font-family:"Lato",sans-serif;color:var(--dark-text)}
.signoff .closing{font-size:15px}
.signature{width:112px;height:18px;background:#e2e2e2;margin:7px 0 9px}
.signoff .name{font-size:13.5px}
.signoff .role{font-size:11px;letter-spacing:-.02em}
.signoff .company{font-size:8px;font-weight:700;text-transform:uppercase;margin-top:4px;letter-spacing:-.02em}
.letterhead .rule{position:absolute;left:42px;top:764px;width:537px;height:2px;background:var(--navy)}
.contact-list{list-style:none;color:var(--body-text)}
.contact-list li{display:flex;align-items:center;gap:4px}
.contact-list svg{flex:none}
.letterhead .contact-list{position:absolute;left:42px;top:788px;font-size:11.5px;line-height:15px}
.address{text-align:right;color:var(--body-text)}
.letterhead .address{position:absolute;right:41px;top:803px;font-size:11.5px;line-height:15.5px}
.footer-band{position:absolute;left:0;bottom:0;display:block}

/* business card front */
.card{position:absolute;left:716px;width:374px;height:213px;overflow:hidden}
.card-front{top:475px;background:var(--paper)}
.card-front .brand{position:absolute;left:17px;top:14px;text-align:center;width:100px}
.card-front .brand .mark-square{width:44px;height:44px;margin-bottom:12px}
.card-front .brand .wordmark{font-size:9px;display:block;margin-left:-14px;width:130px;text-align:left}
.holder{position:absolute;right:18px;top:101px;text-align:right}
.holder .name{font-size:15px;color:var(--navy);font-weight:500;letter-spacing:.02em}
.holder .title{font-size:9px;color:var(--body-text);margin-top:1px}
.card-front .rule{position:absolute;left:17px;top:139px;width:339px;height:1.5px;background:var(--navy)}
.card-front .contact-list{position:absolute;left:17px;top:151px;font-size:9px;line-height:12.8px}
.card-front .address{position:absolute;right:18px;top:164px;font-size:9px;line-height:12.8px}

/* business card back */
.card-back{top:726px;height:214px;background:var(--navy)}
.card-back .brand{position:absolute;left:0;right:0;top:50px;text-align:center}
.card-back .mark-square{width:70px;height:70px;background:#fff;margin-bottom:24px}
.card-back .wordmark{color:#fff;font-size:14px;display:block}
</style>
</head>
<body>

<section class="letterhead">
  <div class="brand">
    <span class="mark-square"></span>
    <span class="wordmark">Tovel &amp; Associates</span>
  </div>

  <p class="salutation">Dear Sir</p>

  <div class="letter-body">
    <p>Lorem ipsum dolor sit amet, an vel recteque dissentiet, detracto albucius platonem ex vel, eros repudiandae cu. Atqui aliquando nec an, unum graece adolescens vel ad. Id odio scae has, iudico euismod atomorum ius ea, cum ea honestatis quaerendum theophrastus. Mea honestatis quaerendum theophrastus. Mea</p>
    <p>Lorem ipsum dolor sit amet, an vel recteque dissentiet, detracto albucius platonem ex vel, eros repudiandae cu. Atqui aliquando nec an, unum graece adolescens vel ad. Id odio scae has, iudico euismod atomorum ius ea, cum ea honestatis quaerendum theophrastus. Mea doming repudiandae ex, cu cum civibus assentior posidonium. Quo etiam pertinax ex, te eros repudiandae cu. Atqui aliquando nec an, unum graece adolescens vel ad. Id odio scae honestatis quaerendum theophrastus. Mea</p>
    <p>Lorem ipsum dolor sit amet, an vel recteque dissentiet, detracto albucius platonem ex vel, eros repudiandae cu. Atqui aliquando nec an, unum graece adolescens vel ad. Id odio scae has, iudico euismod atomorum ius ea, cum ea honestatis quaerendum theophrastus. Mea honestatis quaerendum theophrastus. Mea</p>
    <p>Lorem ipsum dolor sit amet, an vel recteque dissentiet, detracto albucius platonem ex vel, eros repudiandae cu. Atqui aliquando nec an, unum graece adolescens vel ad. Id odio scae has, iudico euismod atomorum ius ea, cum ea honestatis quaerendum theophrastus. Mea honestatis quaerendum theophrastus. Mea</p>
  </div>

  <div class="signoff">
    <p class="closing">Kind Regards</p>
    <div class="signature" role="img" aria-label="Handwritten signature of Edwin Marsh"></div>
    <p class="name">Edwin Marsh</p>
    <p class="role">Head of Lettings</p>
    <p class="company">Tovel &amp; Associates LTD</p>
  </div>

  <div class="rule"></div>

  <ul class="contact-list">
    <li><svg width="8" height="8" viewBox="0 0 10 10"><path d="M2 1l2 2-1 1.5c.8 1.4 1.6 2.2 3 3L7.5 6l2 2-1.5 1.5C5 9 1 5 .5 2z" fill="#1b4f72"/></svg>+44 20 7946 0321</li>
    <li><svg width="8" height="8" viewBox="0 0 10 10"><rect x=".5" y="2" width="9" height="6" fill="none" stroke="#1b4f72"/><path d="M.5 2l4.5 3.5L9.5 2" fill="none" stroke="#1b4f72"/></svg>info@tovelassociates.co</li>
    <li><svg width="8" height="8" viewBox="0 0 10 10"><circle cx="5" cy="5" r="4.3" fill="none" stroke="#1b4f72"/><path d="M.7 5h8.6M5 .7c-2.5 2.8-2.5 5.8 0 8.6M5 .7c2.5 2.8 2.5 5.8 0 8.6" fill="none" stroke="#1b4f72" stroke-width=".8"/></svg>www.tovelassociates.co</li>
  </ul>

  <p class="address">14 Harrow Lane<br>London EC1 4RT</p>

  <svg class="footer-band" width="620" height="28" viewBox="0 0 620 28" aria-hidden="true">
    <path d="M0 5H358C372 5 378 14 392 16H0Z" fill="#2aa3e0"/>
    <path d="M0 18H380C410 18 420 0 460 0H620V28H0Z" fill="#1b4f72"/>
  </svg>
</section>

<div class="brand-standalone" style="position:absolute;left:790px;top:94px;width:310px;text-align:center">
  <span class="mark-square" style="width:150px;height:150px;margin-top:20px"></span>
  <span class="wordmark" style="display:block;font-size:24px;margin-top:46px;margin-left:-40px;margin-right:-40px">Tovel &amp; Associates</span>
</div>

<section class="card card-front">
  <div class="brand">
    <span class="mark-square"></span>
    <span class="wordmark">Tovel &amp; Associates</span>
  </div>
  <div class="holder">
    <p class="name">DANIEL HARLOW</p>
    <p class="title">Director</p>
  </div>
  <div class="rule"></div>
  <ul class="contact-list">
    <li><svg width="6" height="6" viewBox="0 0 10 10"><path d="M2 1l2 2-1 1.5c.8 1.4 1.6 2.2 3 3L7.5 6l2 2-1.5 1.5C5 9 1 5 .5 2z" fill="#1b4f72"/></svg>+44 20 7946 0321</li>
    <li><svg width="6" height="6" viewBox="0 0 10 10"><rect x=".5" y="2" width="9" height="6" fill="none" stroke="#1b4f72"/><path d="M.5 2l4.5 3.5L9.5 2" fill="none" stroke="#1b4f72"/></svg>info@tovelassociates.co</li>
    <li><svg width="6" height="6" viewBox="0 0 10 10"><circle cx="5" cy="5" r="4.3" fill="none" stroke="#1b4f72"/><path d="M.7 5h8.6" stroke="#1b4f72"/></svg>www.tovelassociates.co</li>
  </ul>
  <p class="address">14 Harrow Lane<br>London EC1 4RT</p>
  <svg class="footer-band" width="374" height="16" viewBox="0 0 374 16" aria-hidden="true">
    <path d="M0 2H212C220 2 224 5 230 6H0Z" fill="#2aa3e0"/>
    <path d="M0 8H220C236 8 244 0 266 0H374V16H0Z" fill="#1b4f72"/>
  </svg>
</section>

<section class="card card-back">
  <div class="brand">
    <span class="mark-square"></span>
    <span class="wordmark">Tovel &amp; Associates</span>
  </div>
</section>

</body>
</html>
```